Real Estate Team Business Card

We need a business card designed for our real estate team called "Maplecrest Realty Group". We would like to receive a final format that would allow us to edit the contact information for new employees as they are added to our team. The difficult part of the design is that we will need to have two logos on the card - both our team name logo for "Maplecrest Realty Group" and our company logo for "Summitpoint Real Estate". Most emphasis should be given to the team logo - maybe double the size of our company logo. (we just have to have the company logo somewhere on the card for legal purposes) The design should somehow illustrate we work in real estate, but still use the beehive/bee concept as a lot of our marketing will involve "bee" sayings. We would also like to use the tagline: "find out what all the buzz is about". We also need to use the "fair housing" logo and "realtor" logos. These can both be small like the company logo.
Target Market(s)
Real Estate
Industry/Entity Type
Real Estate Agent
Contact Information for Business Card
Name: Darren Pulaski Title: Realtor Phone: 801-372-5518 Email: darren@maplecrestrealtrygroup.com Website: www.maplecrestrealtygroup.com Facebook: fb/me/maplecrestrealtygroup Twitter: @MaplecrestRltyGrp
Colors
Designer to choose colors to be used in the design.
Requirements
Must have
- Contact information. Maplecrest Realty Group Logo. Summitpoint Real Estate Logo. Realtor logo. Fair Housing Logo. Tagline: "find out what all the buzz is about".
Nice to have
- It would be nice to illustrate that we work in real estate. It would also be nice to somehow incorporate bees or play off of our beehive logo. We will do a lot of marking using sayings like "let us bee the solution" or "real estate meant to bee" etc.

```html
<!DOCTYPE html>
<html lang="en">
<head>
<meta charset="utf-8">
<title>Maplecrest Realty Group – Business Card</title>
<link rel="stylesheet" href="https://fonts.googleapis.com/css2?family=Open+Sans:wght@400;600&display=swap">
<style>
  :root {
    --backdrop: #3a3c3f;
    --honey: #f8c800;
    --honey-deep: #e9b800;
    --paper: #ffffff;
    --ink: #1a1a1a;
    --brand-blue: #1f4fa3;
    --badge: #3b3b3b;
    --tagline: #fff6cc;
  }
  * { box-sizing: border-box; margin: 0; padding: 0; }
  html, body {
    width: 1200px; height: 1000px; overflow: hidden;
    background: var(--backdrop);
    font-family: "Open Sans", Arial, sans-serif;
  }
  .stage {
    position: relative; width: 1200px; height: 1000px;
  }
  .card {
    position: absolute; left: 250px; width: 700px; height: 400px;
    border-radius: 4px; box-shadow: 0 8px 24px rgba(0,0,0,.35);
    overflow: hidden;
  }
  /* back side */
  .card--back {
    top: 70px;
    background: linear-gradient(135deg, var(--honey) 0%, var(--honey) 60%, var(--honey-deep) 100%);
  }
  .badges {
    position: absolute; top: 42px; left: 40px; display: flex; gap: 16px;
  }
  .badge { width: 30px; height: 30px; background: var(--badge); border-radius: 2px; }
  .badge--outline { background: #e9e9e9; border: 3px solid var(--badge); }
  .back-brand {
    position: absolute; right: 44px; bottom: 70px; text-align: center;
  }
  .team-name {
    font-weight: 600; color: var(--ink); letter-spacing: .12em; text-transform: uppercase;
    line-height: 1.15;
  }
  .back-brand .team-name { font-size: 28px; }
  .team-name .sub { display: block; font-size: .5em; letter-spacing: .3em; }
  .tagline {
    margin-top: 14px; font-size: 17px; color: var(--tagline); letter-spacing: .01em;
  }
  /* front side */
  .card--front {
    top: 530px; background: linear-gradient(160deg, var(--paper) 55%, #ececec 100%);
  }
  .company {
    position: absolute; top: 34px; left: 40px;
    font-size: 15px; font-weight: 600; color: var(--brand-blue); line-height: 1.1;
  }
  .company small { display: block; font-size: 8px; letter-spacing: .15em; text-transform: uppercase; }
  .agent { position: absolute; left: 40px; top: 170px; }
  .agent-name {
    font-size: 24px; font-weight: 400; color: var(--honey); text-transform: uppercase;
    letter-spacing: .02em; margin-bottom: 8px;
  }
  .contact-list { list-style: none; }
  .contact-list li {
    display: flex; align-items: center; gap: 10px;
    font-size: 18px; color: var(--ink); line-height: 1.4;
  }
  .contact-list svg { width: 14px; height: 14px; flex: none; fill: var(--honey); }
  .front-brand {
    position: absolute; right: 50px; top: 150px; display: flex; flex-direction: column; align-items: center; gap: 16px;
  }
  .brand-mark { width: 90px; height: 90px; border-radius: 50%; background: var(--honey); }
  .front-brand .team-name { font-size: 32px; text-align: center; }
</style>
</head>
<body>
<main class="stage">
  <section class="card card--back" aria-label="Card back">
    <div class="badges">
      <span class="badge" aria-label="Fair housing badge"></span>
      <span class="badge badge--outline" aria-label="Realtor badge"></span>
    </div>
    <div class="back-brand">
      <p class="team-name">Maplecrest<span class="sub">Realty Group</span></p>
      <p class="tagline">find out what all the buzz is about</p>
    </div>
  </section>

  <section class="card card--front" aria-label="Card front">
    <p class="company">Summitpoint<small>Real Estate</small></p>
    <div class="agent">
      <h1 class="agent-name">Darren Pulaski</h1>
      <ul class="contact-list">
        <li><svg viewBox="0 0 14 14" aria-hidden="true"><path d="M3 1l2.5 3-1.5 1.5c.8 1.8 2.2 3.2 4 4L9.5 8 13 10.5 11.5 13C6 13 1 8 1 2.5z"/></svg>801-372-5518</li>
        <li><svg viewBox="0 0 14 14" aria-hidden="true"><path d="M1 3h12v8H1z M1 3l6 5 6-5" stroke="#fff" stroke-width="1"/></svg>darren@maplecrestrealtrygroup.com</li>
        <li><svg viewBox="0 0 14 14" aria-hidden="true"><circle cx="7" cy="7" r="6"/></svg>www.maplecrestrealtygroup.com</li>
        <li><svg viewBox="0 0 14 14" aria-hidden="true"><rect x="1" y="1" width="12" height="12" rx="2"/></svg>fb/me/maplecrestrealtygroup</li>
        <li><svg viewBox="0 0 14 14" aria-hidden="true"><circle cx="7" cy="7" r="6"/></svg>@MaplecrestRltyGrp</li>
      </ul>
    </div>
    <div class="front-brand">
      <span class="brand-mark" aria-hidden="true"></span>
      <p class="team-name">Maplecrest<span class="sub">Realty Group</span></p>
    </div>
  </section>
</main>
</body>
</html>
```